Business card design for international hub site

I need a business card design with the logo attached. Although the site is for the teenage audience (it is about the high school graduation ball, the Prom), the business card is for professional use to be given to professional contacts (B2B), such as suppliers and partners, so it needs to look professional (but also girly, glamours and clean).

Target Market(s)

B2B

Industry/Entity Type

Media

Colors
eea4c8
f9d9e8
e667a6
9d9d9d
1b1b1b

Requirements
Must have
• Space for Name, Tile, Address, Phone, email and website.
Should not have
• Photo

```html
<!DOCTYPE html>
<html lang="en">
<head>
<meta charset="utf-8">
<title>The Gala Hive – Business Card</title>
<link rel="stylesheet" href="https://fonts.googleapis.com/css2?family=EB+Garamond:wght@400;600&family=Great+Vibes&display=swap">
<style>
  :root {
    --page-bg: #ececec;
    --card-dark: #1b1b1b;
    --card-dark-2: #262626;
    --card-light: #ffffff;
    --pink-deep: #e667a6;
    --pink-mid: #eea4c8;
    --pink-soft: #f9d9e8;
    --ink: #1b1b1b;
    --grey: #9d9d9d;
    --white: #ffffff;
  }
  * { margin: 0; padding: 0; box-sizing: border-box; }
  html, body { width: 1200px; height: 586px; overflow: hidden; }
  body {
    position: relative;
    background: var(--page-bg);
    font-family: "EB Garamond", Georgia, serif;
  }
  .card {
    position: absolute;
    top: 129px;
    width: 502px;
    height: 301px;
    overflow: hidden;
  }
  /* Front */
  .card--front {
    left: 62px;
    background: var(--card-dark);
  }
  .front-texture {
    position: absolute; inset: 0;
    background: linear-gradient(135deg, var(--card-dark-2) 0%, var(--card-dark) 55%, var(--card-dark-2) 100%);
  }
  .brand-name {
    position: absolute;
    left: 0; right: 0;
    top: 106px;
    text-align: center;
    color: var(--white);
    font-weight: 400;
    font-size: 46px;
    line-height: 1;
    letter-spacing: 0.5px;
  }
  .brand-name .mark-dot {
    display: inline-block;
    width: 10px; height: 10px;
    border-radius: 50%;
    background: var(--white);
    vertical-align: middle;
    margin-right: 12px;
    position: relative; top: -4px;
  }
  .website {
    position: absolute;
    left: 0; right: 0;
    top: 257px;
    text-align: center;
    color: var(--white);
    font-weight: 600;
    font-size: 12px;
    letter-spacing: 3.2px;
  }
  /* Back */
  .card--back {
    left: 619px;
    background: var(--card-light);
  }
  .floral-panel {
    position: absolute;
    left: 0; top: 0;
    width: 175px; height: 100%;
    background: linear-gradient(90deg, var(--pink-deep) 0%, var(--pink-mid) 55%, rgba(249,217,232,0) 100%);
  }
  .floral-faint {
    position: absolute;
    right: 0; top: 0;
    width: 140px; height: 100%;
    background: linear-gradient(270deg, rgba(249,217,232,0.7) 0%, rgba(249,217,232,0) 100%);
  }
  .holder-name {
    position: absolute;
    right: 56px;
    top: 70px;
    font-family: "Great Vibes", cursive;
    font-size: 38px;
    color: var(--pink-deep);
    line-height: 1;
  }
  .contact-list {
    position: absolute;
    right: 56px;
    top: 136px;
    list-style: none;
    text-align: right;
  }
  .contact-list li {
    display: flex;
    justify-content: flex-end;
    align-items: center;
    height: 24.5px;
    font-size: 13px;
    color: var(--ink);
  }
  .contact-list svg {
    width: 14px; height: 12px;
    margin-left: 9px;
    fill: var(--pink-deep);
  }
  .address {
    position: absolute;
    right: 70px;
    top: 216px;
    text-align: right;
    font-style: normal;
    font-size: 13px;
    line-height: 19px;
    color: var(--pink-deep);
  }
</style>
</head>
<body>

<section class="card card--front" aria-label="Card front">
  <div class="front-texture" role="img" aria-label="Dark faceted geometric background pattern"></div>
  <h1 class="brand-name"><span class="mark-dot"></span>The Gala Hive</h1>
  <p class="website">www.thegalahive.com</p>
</section>

<section class="card card--back" aria-label="Card back">
  <div class="floral-panel" role="img" aria-label="Pink swirling floral ornament"></div>
  <div class="floral-faint" role="img" aria-label="Faint pink floral flourish"></div>

  <h2 class="holder-name">Mara Ellison</h2>

  <ul class="contact-list">
    <li>+44 (0)1632 960481
      <svg viewBox="0 0 14 12" aria-label="Phone"><path d="M1 4c0-2 3-3 6-3s6 1 6 3v1h-3V3.5H4V5H1z"/><path d="M3 6h8l1.5 5h-11z"/></svg>
    </li>
    <li>(555) 014-2290
      <svg viewBox="0 0 14 12" aria-label="Fax"><rect x="4" y="0" width="6" height="3"/><rect x="0" y="3.5" width="14" height="5" rx="1"/><rect x="3" y="7" width="8" height="5"/></svg>
    </li>
    <li>hello@thegalahive.com
      <svg viewBox="0 0 14 12" aria-label="Email"><path d="M0 1h14v10H0z" fill="none"/><path d="M0 1h14L7 7z"/><path d="M0 2.5l7 5.5 7-5.5V11H0z"/></svg>
    </li>
  </ul>

  <address class="address">
    Elm Court, Hartley<br>
    Ashford, KX4 2PL
  </address>
</section>

</body>
</html>
```